Business card design for Automotive workshop

We need a business card for a new automotive repair and tyre shop called Keelstone Prime Automotive located in New Zealand. We are a clean, modern and fresh workshop and company.

Front needs to feature logo,
my name:
Marlo Fenwicke (director)

Address:
48 Tarn Lane
Karoha Bay 3592

Phone: 07 594 2713
Mobile: 027 451 9362
Email: office@keelstoneautomotive.example.nz
Website: keelstoneautomotive.example.nz

Back needs to feature an area to write down appointment details, date and time.

Also feature a list of jobs and work we do such as,
Vehicle Servicing
All Mechanical Repairs
Warrant of Fitness
Tyres & Wheel Alignments
Automotive Diagnostics
Automotive Parts & Supplies

```html
<!DOCTYPE html>
<html lang="en">
<head>
<meta charset="utf-8">
<title>Keelstone Prime Automotive – Business Card</title>
<link href="https://fonts.googleapis.com/css2?family=Arimo:ital,wght@0,400;0,700;1,400&display=swap" rel="stylesheet">
<style>
  :root {
    --stage: #3a3a3a;
    --ink: #0b0b0b;
    --red: #b8222a;
    --red-deep: #9c1b20;
    --red-bright: #d02a30;
    --white: #ffffff;
    --bullet: #e0262d;
  }
  * { box-sizing: border-box; margin: 0; padding: 0; }
  html, body {
    width: 1200px; height: 1195px; overflow: hidden;
    background: var(--stage);
    font-family: "Arimo", Arial, sans-serif;
  }
  .stage {
    position: relative; width: 1200px; height: 1195px;
    display: flex; flex-direction: column; align-items: center;
    justify-content: center; gap: 44px;
  }
  .card {
    position: relative; width: 880px; height: 503px;
    overflow: hidden; box-shadow: 0 10px 30px rgba(0,0,0,.45);
  }

  /* Back side */
  .card--back { background: var(--ink); color: var(--white); }
  .card--back .decor {
    position: absolute; right: -60px; top: -40px; width: 460px; height: 380px;
    border-radius: 50%;
    background: radial-gradient(circle at 50% 55%, #262626 0%, #1a1a1a 45%, rgba(11,11,11,0) 72%);
  }
  .card--back .brand {
    position: absolute; left: 300px; top: 62px;
    font-size: 34px; font-weight: 700; color: var(--bullet); letter-spacing: 1px;
    white-space: nowrap;
  }
  .service-list { position: absolute; list-style: none; font-size: 23px; line-height: 33px; white-space: nowrap; }
  .service-list li { position: relative; padding-left: 20px; }
  .service-list li::before {
    content: ""; position: absolute; left: 0; top: 13px;
    width: 10px; height: 10px; border-radius: 50%; background: var(--bullet);
  }
  .service-list--left { left: 70px; top: 200px; }
  .service-list--right { left: 480px; top: 170px; }
  .appt-field { position: absolute; display: flex; align-items: center; gap: 14px; font-size: 23px; }
  .appt-field .label { position: relative; padding-left: 20px; }
  .appt-field .label::before {
    content: ""; position: absolute; left: 0; top: 8px;
    width: 10px; height: 10px; border-radius: 50%; background: var(--bullet);
  }
  .appt-field .blank { width: 260px; height: 48px; border-radius: 24px; background: var(--white); }
  .appt-field--date { left: 70px; top: 400px; }
  .appt-field--time { left: 480px; top: 310px; }

  /* Front side */
  .card--front {
    background: linear-gradient(115deg, var(--red-deep) 0%, var(--red-bright) 40%, var(--red) 60%, var(--red-deep) 100%);
    color: var(--ink);
  }
  .card--front .decor {
    position: absolute; left: 120px; top: 200px; width: 740px; height: 260px;
    border-radius: 130px;
    background: radial-gradient(ellipse at 40% 60%, rgba(230,90,80,.35) 0%, rgba(230,90,80,.15) 50%, rgba(230,90,80,0) 75%);
  }
  .person { position: absolute; left: 70px; top: 70px; }
  .person__name {
    display: flex; align-items: center; gap: 12px;
    font-size: 36px; font-weight: 700; letter-spacing: 1px;
  }
  .person__name .dot { width: 30px; height: 30px; border-radius: 50%; background: var(--ink); flex: none; }
  .person__role { margin-left: 30px; font-size: 26px; margin-top: 2px; }
  .person__rule { width: 360px; height: 8px; border-radius: 4px; background: var(--ink); margin-top: 8px; }
  .contact-list { position: absolute; left: 70px; top: 245px; list-style: none; font-size: 22px; font-style: italic; line-height: 38px; white-space: nowrap; }
  .contact-list li { display: flex; align-items: center; gap: 12px; }
  .contact-list svg { width: 24px; height: 24px; flex: none; }
  .card--front .brand {
    position: absolute; right: 50px; top: 180px;
    font-size: 34px; font-weight: 700; color: var(--white); letter-spacing: 1px;
    white-space: nowrap;
  }
</style>
</head>
<body>
<main class="stage">

  <section class="card card--back" aria-label="Card back">
    <div class="decor" role="img" aria-label="Faint turbocharger illustration"></div>
    <div class="brand">Keelstone Prime Automotive</div>
    <ul class="service-list service-list--left">
      <li>Vehicle Servicing</li>
      <li>All Mechanical Repairs</li>
      <li>Warrant of Fitness</li>
    </ul>
    <ul class="service-list service-list--right">
      <li>Tyres &amp; Wheel Alignments</li>
      <li>Automotive Parts &amp; Supplies</li>
      <li>Automotive Diagnostics</li>
    </ul>
    <div class="appt-field appt-field--date"><span class="label">Date</span><span class="blank"></span></div>
    <div class="appt-field appt-field--time"><span class="label">Time</span><span class="blank"></span></div>
  </section>

  <section class="card card--front" aria-label="Card front">
    <div class="decor" role="img" aria-label="Faint car and wrench illustration"></div>
    <div class="person">
      <div class="person__name"><span class="dot"></span>Marlo Fenwicke</div>
      <div class="person__role">(Managing director)</div>
      <div class="person__rule"></div>
    </div>
    <ul class="contact-list">
      <li>
        <svg viewBox="0 0 24 24"><circle cx="12" cy="12" r="12" fill="#0b0b0b"/><path d="M8 6l2 0 1 3-1.5 1a7 7 0 0 0 4 4l1-1.5 3 1v2a2 2 0 0 1-2 2A10 10 0 0 1 6 8a2 2 0 0 1 2-2z" fill="#b8222a"/></svg>
        027 451 9362
      </li>
      <li>
        <svg viewBox="0 0 24 24"><circle cx="12" cy="12" r="12" fill="#0b0b0b"/><rect x="6" y="10" width="12" height="7" rx="1" fill="#b8222a"/><path d="M5 10a7 3 0 0 1 14 0v1H5z" fill="#b8222a"/></svg>
        07 594 2713
      </li>
      <li>
        <svg viewBox="0 0 24 24"><circle cx="12" cy="12" r="12" fill="#0b0b0b"/><rect x="5" y="8" width="14" height="9" fill="#b8222a"/><path d="M5 8l7 5 7-5" stroke="#0b0b0b" stroke-width="1.5" fill="none"/></svg>
        office@keelstoneautomotive.example.nz
      </li>
      <li>
        <svg viewBox="0 0 24 24"><circle cx="12" cy="12" r="12" fill="#0b0b0b"/><circle cx="12" cy="12" r="7" fill="none" stroke="#b8222a" stroke-width="1.6"/><path d="M5 12h14M12 5c-3 4-3 10 0 14M12 5c3 4 3 10 0 14" stroke="#b8222a" stroke-width="1.4" fill="none"/></svg>
        keelstoneautomotive.example.nz
      </li>
      <li>
        <svg viewBox="0 0 24 24"><circle cx="12" cy="12" r="12" fill="#0b0b0b"/><path d="M5 12l7-6 7 6h-2v6h-3v-4h-4v4H7v-6z" fill="#b8222a"/></svg>
        48 Tarn Lane Karoha Bay 3592
      </li>
    </ul>
    <div class="brand">Keelstone Prime Automotive</div>
  </section>

</main>
</body>
</html>
```